Bookcover: Ways to Turn Into a Bold Pathfinder

I am publishing a super-low-cost innovation book for €4,99 on Quillmere Open Press to help everyone become a great innovator: young ambitious people without college education nor a big budget. Do you want to help me?

Brief:
Design a book cover 1600 x 2560 pixels for QOP.
Main title: Ways to Turn Into a Bold Pathfinder
Sub title: mindset - insights - skills & tools
Author: Joost ter Brakel
Design: captive, and appealing to everyone
Target Group: young ambitious people without college education

For quillmere please format the height/width ratio of 1.6:1

```html
<!DOCTYPE html>
<html lang="en">
<head>
<meta charset="utf-8">
<title>Ways to Turn Into a Bold Pathfinder — Book Cover</title>
<link rel="stylesheet" href="https://fonts.googleapis.com/css2?family=Montserrat:wght@500;600;700&family=Poppins:wght@800&display=swap">
<style>
  :root {
    --backdrop: #8e8e8e;
    --cover-yellow: #e0a82b;
    --cover-yellow-deep: #d99a20;
    --ink-dark: #2f2f2f;
    --accent-maroon: #7b2a3e;
    --band-dark: #262626;
    --band-text: #f2f2f2;
  }
  * { margin: 0; padding: 0; box-sizing: border-box; }
  html, body {
    width: 1200px;
    height: 1200px;
    overflow: hidden;
    background: var(--backdrop);
  }
  .book-cover {
    position: absolute;
    left: 250px;
    top: 40px;
    width: 700px;
    height: 1120px;
    background: linear-gradient(180deg, var(--cover-yellow) 0%, var(--cover-yellow-deep) 100%);
    overflow: hidden;
  }
  .spotlight-beam {
    position: absolute;
    left: 0;
    top: 0;
    width: 700px;
    height: 560px;
  }
  .cover-emblem {
    position: absolute;
    left: 190px;
    top: 140px;
    width: 320px;
    height: 320px;
    border-radius: 40px;
    background: radial-gradient(ellipse at center, rgba(51,51,51,0.85) 0%, rgba(51,51,51,0.55) 55%, rgba(51,51,51,0) 78%);
  }
  .title-block {
    position: absolute;
    left: 0;
    width: 100%;
    text-align: center;
    color: var(--ink-dark);
    white-space: nowrap;
  }
  .title-lead {
    font-family: "Montserrat", sans-serif;
    font-weight: 700;
    font-variant: small-caps;
    font-size: 52px;
    letter-spacing: 0.03em;
    line-height: 1;
  }
  .title-lead.line-one { top: 514px; }
  .title-lead.line-two { top: 580px; }
  .title-main {
    top: 640px;
    font-family: "Poppins", sans-serif;
    font-weight: 800;
    font-size: 80px;
    letter-spacing: 0.12em;
    line-height: 1;
    color: var(--accent-maroon);
    padding-left: 0.12em;
  }
  .subtitle-item {
    position: absolute;
    left: 0;
    width: 100%;
    text-align: center;
    font-family: "Montserrat", sans-serif;
    font-weight: 500;
    font-variant: small-caps;
    font-size: 36px;
    letter-spacing: 0.16em;
    line-height: 1;
    color: var(--ink-dark);
    white-space: nowrap;
  }
  .subtitle-item.mindset { top: 787px; }
  .subtitle-item.insights { top: 861px; }
  .subtitle-item.skills { top: 934px; }
  .author-band {
    position: absolute;
    left: 0;
    bottom: 0;
    width: 100%;
    height: 58px;
    background: var(--band-dark);
    display: flex;
    align-items: center;
    justify-content: center;
  }
  .author-name {
    font-family: "Montserrat", sans-serif;
    font-weight: 600;
    font-size: 22px;
    letter-spacing: 0.1em;
    text-transform: uppercase;
    color: var(--band-text);
  }
</style>
</head>
<body>
  <main class="book-cover">
    <svg class="spotlight-beam" viewBox="0 0 700 560" aria-hidden="true">
      <defs>
        <linearGradient id="beamFade" x1="0" y1="0" x2="0" y2="1">
          <stop offset="0" stop-color="#ffffff" stop-opacity="0.85"/>
          <stop offset="0.55" stop-color="#ffffff" stop-opacity="0.3"/>
          <stop offset="1" stop-color="#ffffff" stop-opacity="0"/>
        </linearGradient>
      </defs>
      <polygon points="210,0 490,0 700,560 0,560" fill="url(#beamFade)"/>
    </svg>

    <div class="cover-emblem" role="img" aria-label="Lightbulb with circuit filament and two gears, dark grey emblem"></div>

    <h1>
      <span class="title-block title-lead line-one">Ways to</span>
      <span class="title-block title-lead line-two">Turn Into a Bold</span>
      <span class="title-block title-main">Pathfinder</span>
    </h1>

    <p class="subtitle-item mindset">Mindset</p>
    <p class="subtitle-item insights">Insights</p>
    <p class="subtitle-item skills">Skills &amp; Tools</p>

    <footer class="author-band">
      <span class="author-name">Joost ter Brakel</span>
    </footer>
  </main>
</body>
</html>
```